TL - business card

Tallow Partners is an insurance brokerage firm, inovative, proactive, vigorous, which aims to become the leader of the insurance brokers in Anfrica. We should like to get some designs which should be avoided also in Gray / Metallic for the Administration and Orange / Blue for the Managers (ike in the picture sent). The Blue / Green logo is not the correct one, but the source of the file. Please adjust the color accordingly for the business cards. 1 / Orange / Blue 2 / Gray / Metallic We want something classic but which is transmitted strenght, inovation, modernity and most of all, rapidity. We want something start-up like, very punchy and catching eye remaining profesional at the same time. Name: Dorian Whitlock Function: Managing Director Address: N ° 17/18 Rua Veloso - R / C 2B Direita - Bairro Mutamba - Luanda Tel: (+244) 947 582 316 Email: dorian.whitlock@tallow-p.example Website: www.tallow-p. example We want classic in the front and creative, colorfull at the back. The cards will be printed in relief, with very high quality of paper.
Insurance Broker
Colors
Designer to choose colors to be used in the design.

```html
<!DOCTYPE html>
<html lang="en">
<head>
<meta charset="utf-8">
<title>Tallow Partners – Business Card</title>
<link rel="stylesheet" href="https://fonts.googleapis.com/css2?family=Exo+2:wght@700&family=Roboto:wght@400;500;700&display=swap">
<style>
  :root {
    --brand-green: #0a9444;
    --brand-blue: #29a8e0;
    --ink-gray: #4a4a4a;
    --muted-gray: #8a8a8a;
    --card-white: #ffffff;
    --backdrop: #e6e7e9;
  }
  * { box-sizing: border-box; margin: 0; padding: 0; }
  html, body { width: 1200px; height: 960px; overflow: hidden; }
  body {
    background: var(--backdrop);
    font-family: "Roboto", Arial, sans-serif;
    position: relative;
  }
  .card {
    position: absolute;
    left: 220px;
    width: 760px;
    height: 434px;
    background: var(--card-white);
    border-bottom: 5px solid var(--brand-green);
    box-shadow: 0 6px 18px rgba(0,0,0,0.12);
    overflow: hidden;
  }
  .card--brand { top: 30px; }
  .card--contact { top: 496px; }

  /* Brand side */
  .brand-lockup {
    position: absolute;
    left: 0; right: 0; top: 150px;
    display: flex;
    align-items: center;
    justify-content: center;
    gap: 18px;
  }
  .brand-dot {
    width: 56px; height: 56px;
    border-radius: 50%;
    background: var(--brand-green);
  }
  .brand-name {
    font-family: "Exo 2", Arial, sans-serif;
    font-weight: 700;
    font-size: 46px;
    letter-spacing: 1px;
    color: var(--brand-green);
    text-transform: uppercase;
  }
  .brand-web {
    position: absolute;
    left: 0; right: 0; top: 250px;
    text-align: center;
    font-size: 17px;
    letter-spacing: 7px;
    color: var(--ink-gray);
  }

  /* Contact side */
  .mark-ring {
    position: absolute;
    left: 44px; top: 52px;
    width: 330px; height: 330px;
  }
  .contact-block {
    position: absolute;
    right: 42px; top: 48px;
    width: 360px;
    text-align: right;
  }
  .contact-brand {
    font-family: "Exo 2", Arial, sans-serif;
    font-weight: 700;
    font-size: 27px;
    color: var(--brand-green);
    text-transform: uppercase;
    letter-spacing: 0.5px;
  }
  .person-name {
    margin-top: 30px;
    font-weight: 700;
    font-size: 27px;
    color: var(--brand-green);
  }
  .person-role {
    font-weight: 500;
    font-size: 18px;
    color: var(--brand-blue);
    margin-top: 2px;
  }
  .address {
    margin-top: 12px;
    font-size: 16px;
    line-height: 22px;
    color: var(--ink-gray);
    font-style: normal;
  }
  .contact-list {
    list-style: none;
    margin-top: 14px;
    font-size: 16px;
    line-height: 24px;
    color: var(--ink-gray);
  }
  .contact-list li {
    display: flex;
    justify-content: flex-end;
    align-items: center;
    gap: 10px;
  }
  .contact-icon { width: 15px; height: 15px; fill: var(--brand-green); flex: none; }
  .contact-icon--blank { visibility: hidden; }
</style>
</head>
<body>

<section class="card card--brand">
  <div class="brand-lockup">
    <span class="brand-dot"></span>
    <span class="brand-name">Tallow Partners</span>
  </div>
  <p class="brand-web">www.tallow-p.example</p>
</section>

<section class="card card--contact">
  <svg class="mark-ring" viewBox="0 0 330 330" aria-hidden="true">
    <circle cx="165" cy="165" r="150" fill="none" stroke="var(--brand-green)" stroke-width="16"/>
  </svg>

  <div class="contact-block">
    <p class="contact-brand">Tallow Partners</p>
    <p class="person-name">Dorian Whitlock</p>
    <p class="person-role">Managing Director</p>
    <address class="address">
      N ° 17/18 Rua Veloso<br>
      R / C 2B Direita<br>
      Bairro Mutamba, Luanda
    </address>
    <ul class="contact-list">
      <li>(+244) 947 582 316
        <svg class="contact-icon" viewBox="0 0 24 24" aria-hidden="true"><path d="M6.6 10.8a15.1 15.1 0 0 0 6.6 6.6l2.2-2.2a1 1 0 0 1 1-.25 11.4 11.4 0 0 0 3.6.57 1 1 0 0 1 1 1V20a1 1 0 0 1-1 1A17 17 0 0 1 3 4a1 1 0 0 1 1-1h3.5a1 1 0 0 1 1 1c0 1.25.2 2.45.57 3.57a1 1 0 0 1-.25 1z"/></svg>
      </li>
      <li>dorian.whitlock@tallow-p.example
        <svg class="contact-icon" viewBox="0 0 24 24" aria-hidden="true"><path d="M2 5h20v14H2z M3 6l9 7 9-7" fill="none" stroke="var(--brand-green)" stroke-width="2"/></svg>
      </li>
      <li>www.tallow-p.example
        <svg class="contact-icon" viewBox="0 0 24 24" aria-hidden="true"><circle cx="12" cy="12" r="10" fill="none" stroke="var(--brand-green)" stroke-width="2"/><path d="M2 12h20M12 2c3 3 3 17 0 20M12 2c-3 3-3 17 0 20" fill="none" stroke="var(--brand-green)" stroke-width="1.6"/></svg>
      </li>
    </ul>
  </div>
</section>

</body>
</html>
```